Danielle Brooke Interiors business cards

We need a DOUBLE SIDED business card design that is simple, elegant and modern. We are a rapidly growing Interior Design Firm, and our brand colours are blush pink, navy, and antique gold, so we require some or all of these colours to be used. The final design should portray elegance, simplicity, and have a modern feel. We have upload inspiration photos that have the feel we're looking for.

Industry/Entity Type

Interior Design

Contact Information for Business Card

Contact information and LOGO

Colors
EB3D1F
EC4F4E
F09395
F8D3D4
FCEDEE

Requirements
Must have
• Navy, the right shade of blush pink, and antique gold

```html
<!DOCTYPE html>
<html lang="en">
<head>
<meta charset="utf-8">
<title>Danielle Brooke Interiors – Business Cards</title>
<link href="https://fonts.googleapis.com/css2?family=Jost:wght@400&family=Open+Sans:wght@400;600;700;800&display=swap" rel="stylesheet">
<style>
  :root {
    --navy: #212859;
    --gold: #9c7e50;
    --blush: #fcedee;
    --accent: #eb3d1f;
    --page: #ffffff;
  }
  * { box-sizing: border-box; margin: 0; padding: 0; }
  html, body { width: 1200px; height: 900px; overflow: hidden; background: var(--page); }
  .canvas { position: relative; width: 1200px; height: 900px; }

  .card {
    position: absolute;
    left: 263px;
    width: 675px;
    height: 405px;
    background: var(--blush);
    overflow: hidden;
  }
  .card--front { top: 24px; }
  .card--back { top: 471px; }

  .band {
    position: absolute;
    left: 0;
    width: 100%;
    height: 57px;
    display: flex;
  }
  .band--top { top: 0; }
  .band--bottom { bottom: 0; }
  .band__navy { width: 338px; background: var(--navy); }
  .band__gold { flex: 1; background: var(--gold); }

  .wordmark {
    position: absolute;
    font-family: "Jost", sans-serif;
    font-weight: 400;
    color: var(--gold);
    text-transform: uppercase;
    text-align: center;
    line-height: 1.25;
  }
  .card--front .wordmark {
    left: 0; right: 0;
    top: 186px;
    font-size: 28px;
    letter-spacing: 3px;
  }
  .card--back .wordmark {
    left: 330px; /* placeholder, overridden below */
  }
  .card--back .wordmark {
    left: 50px;
    width: 272px;
    top: 170px;
    font-size: 24px;
    letter-spacing: 2px;
  }

  .divider {
    position: absolute;
    left: 337px;
    top: 114px;
    width: 2px;
    height: 177px;
    background: var(--navy);
  }

  .contact-block {
    position: absolute;
    left: 358px;
    top: 90px;
    font-family: "Open Sans", sans-serif;
    color: var(--navy);
  }
  .contact-block__name {
    font-size: 28px;
    font-weight: 800;
    line-height: 1;
    letter-spacing: 0.3px;
  }
  .contact-block__title {
    font-size: 16px;
    font-weight: 700;
    margin-top: 3px;
  }
  .contact-list {
    list-style: none;
    margin-top: 58px;
  }
  .contact-list li {
    display: flex;
    align-items: center;
    gap: 6px;
    font-size: 16px;
    font-weight: 400;
    height: 26px;
  }
  .contact-list svg { width: 20px; height: 20px; flex: none; }
</style>
</head>
<body>
<main class="canvas">

  <section class="card card--front" aria-label="Business card front">
    <div class="band band--top"><div class="band__navy"></div><div class="band__gold"></div></div>
    <p class="wordmark">Danielle Brooke Interiors</p>
    <div class="band band--bottom"><div class="band__navy"></div><div class="band__gold"></div></div>
  </section>

  <section class="card card--back" aria-label="Business card back">
    <div class="band band--top"><div class="band__navy"></div><div class="band__gold"></div></div>

    <p class="wordmark">Danielle Brooke<br>Interiors</p>

    <div class="divider"></div>

    <div class="contact-block">
      <h1 class="contact-block__name">DANIELLE BROOKE</h1>
      <p class="contact-block__title">PRINCIPAL DESIGNER</p>
      <ul class="contact-list">
        <li>
          <svg viewBox="0 0 24 24" aria-hidden="true">
            <path d="M6.5 3 L9.5 3 L10.5 8 L8.2 9.6 C9.3 12.2 11.3 14.3 13.9 15.6 L15.6 13.3 L20.5 14.3 L20.5 17.5 C20.5 19 19.3 20.5 17.6 20.3 C10.2 19.5 4.4 13.7 3.7 6.3 C3.6 4.6 4.9 3 6.5 3 Z" fill="var(--accent)"/>
            <path d="M14 3.5 A6.5 6.5 0 0 1 20.5 10" fill="none" stroke="var(--accent)" stroke-width="1.6" stroke-linecap="round"/>
            <path d="M14 6.5 A3.5 3.5 0 0 1 17.5 10" fill="none" stroke="var(--accent)" stroke-width="1.6" stroke-linecap="round"/>
          </svg>
          <span>555 204 7318</span>
        </li>
        <li>
          <svg viewBox="0 0 24 24" aria-hidden="true">
            <circle cx="12" cy="12" r="4" fill="none" stroke="var(--accent)" stroke-width="2.4"/>
            <path d="M16 8 V14 C16 16.5 20.5 16.5 20.5 12 A8.5 8.5 0 1 0 16.5 19.3" fill="none" stroke="var(--accent)" stroke-width="2.4" stroke-linecap="round"/>
          </svg>
          <span>danielle@dbinteriorsco.com</span>
        </li>
        <li>
          <svg viewBox="0 0 24 24" aria-hidden="true">
            <circle cx="12" cy="12" r="9" fill="none" stroke="var(--accent)" stroke-width="2"/>
            <ellipse cx="12" cy="12" rx="4" ry="9" fill="none" stroke="var(--accent)" stroke-width="1.6"/>
            <path d="M3 12 H21 M4.5 7.5 H19.5 M4.5 16.5 H19.5" stroke="var(--accent)" stroke-width="1.6"/>
          </svg>
          <span>www.daniellebrookeinteriors.com</span>
        </li>
      </ul>
    </div>

    <div class="band band--bottom"><div class="band__navy"></div><div class="band__gold"></div></div>
  </section>

</main>
</body>
</html>
```